Satchel & Sundial needs new business card design

I need a new business card design. I'm looking for out-of-the-box design which represents the freedom of being a location independent entrepreneur.
I offer coaching, retreats and trips.
I would like to see designs with and without the photo.
Colors I use are black (#000000), green (#25A796) and brown (#D7C38C)
Website satchelandsundial.example

Target Market(s)

location independent entrepreneurs, digital nomads, people looking to swap the 9 to 5 for a lifestyle business

Industry/Entity Type

Business

Contact Information for Business Card

Dorota Falkner
Your Lifestyle Business Coach, Retreat & Trip Leader
http://satchelandsundial.example
hello@satchelandsundial.example
Live a life you don't need a holiday from

Font styles to use
Serif
Sans Serif

Requirements
Must have
• One side should contain only the logo. I would also consider having the "Live a life you don't need a holiday from" on that side too (depending on how it looks)
• Please show both sides on the designs.

```html
<!DOCTYPE html>
<html lang="en">
<head>
<meta charset="utf-8">
<title>Satchel &amp; Sundial — Business Card</title>
<link rel="stylesheet" href="https://fonts.googleapis.com/css2?family=Source+Sans+3:ital,wght@0,400;0,600;1,700&display=swap">
<style>
  :root {
    --backdrop: #808080;
    --card-sand: #d7c38c;
    --card-black: #1b1b1b;
    --ink: #1a1a1a;
    --ink-light: #ffffff;
    --accent-green: #25a796;
  }
  html, body {
    margin: 0;
    padding: 0;
    width: 1200px;
    height: 900px;
    overflow: hidden;
    background: var(--backdrop);
    font-family: "Source Sans 3", "Helvetica Neue", Arial, sans-serif;
  }
  .canvas {
    position: relative;
    width: 1200px;
    height: 900px;
  }
  .card {
    position: absolute;
    top: 271px;
    width: 457px;
    height: 281px;
    border-radius: 14px;
    overflow: hidden;
  }
  .card--front { left: 137px; background: var(--card-sand); color: var(--ink); }
  .card--back  { left: 626px; background: var(--card-black); color: var(--ink-light); }

  .brand-name {
    position: absolute;
    margin: 0;
    font-weight: 600;
    letter-spacing: 0.5px;
    white-space: nowrap;
  }
  .card--front .brand-name {
    left: 38px;
    top: 94px;
    font-size: 24px;
    color: var(--ink);
  }
  .card--back .brand-name {
    left: 0;
    right: 0;
    top: 110px;
    text-align: center;
    font-size: 34px;
    color: var(--ink-light);
  }

  .person {
    position: absolute;
    left: 250px;
    top: 92px;
    line-height: 16px;
  }
  .person__name {
    margin: 0 0 4px;
    font-size: 15px;
    font-weight: 600;
  }
  .person__role {
    margin: 0;
    font-size: 12.5px;
    font-weight: 400;
  }

  .divider {
    position: absolute;
    left: 0;
    right: 0;
    top: 179px;
    height: 1.5px;
    background: #3a3320;
  }

  .contact {
    position: absolute;
    left: 0;
    right: 0;
    top: 196px;
    text-align: center;
    font-size: 13px;
    line-height: 16px;
  }
  .contact p { margin: 0; }
  .tagline {
    margin-top: 7px !important;
    font-size: 14px;
    font-weight: 700;
    font-style: italic;
  }
</style>
</head>
<body>
<main class="canvas">
  <section class="card card--front" aria-label="Card front">
    <h1 class="brand-name">Satchel &amp; Sundial</h1>
    <div class="person">
      <p class="person__name">Dorota Falkner</p>
      <p class="person__role">Your Lifestyle Business Coach</p>
      <p class="person__role">Retreat &amp; Trip Leader</p>
    </div>
    <div class="divider"></div>
    <div class="contact">
      <p>hello@satchelandsundial.example</p>
      <p>www.satchelandsundial.example</p>
      <p class="tagline">Live a life you don't need a holiday from</p>
    </div>
  </section>

  <section class="card card--back" aria-label="Card back">
    <h2 class="brand-name">Satchel &amp; Sundial</h2>
  </section>
</main>
</body>
</html>
```